Meadowfield Baptist Church Banner Design

Designing 6 banners (3 + 3 that will hang on opposite sides of our auditorium) that are 10 feet long by 4 feet wide.

Use our branding guide - specifically item 4 (vertical logo) and item 5 (icon logo).

Design elements found in our KINDLE booklet, we would like to see designs that utilize the white, green and blue colour palettes but NOT the grey. Other colours may be incorporated (e.g. coral).

We are looking for 3 banner designs that would match on either side of the auditorium, the first banner incorporating the word "TRUTH", the second incorporating the word "LOVE", and the third incorporating the word "MISSION".

We interested in incorporating graphics such as trees or outdoor themes.

Font styles to use
Other font styles liked:
• Montserrat

Colors
34a7d7
00a990
f47c35

Requirements
Must have
• Banner Type #1 include the word "TRUTH"
Banner Type #2 include the word "LOVE"
Banner Type #3 include the word "MISSION"

Colour scheme must include CMYK 54 / 5 / 16 / 0 (which is available in the branding guide.) We have selected the three colours, included below in the brief.

From the branding guide - utilize #5 (icon) for the banner.

UPDATE: After reviewing the initial submissions, we are asking for designs that ONLY incorporate #5 - the ICON logo for the banners.
Nice to have
• It would be nice to have some creativity with the colour ... though a more minimalistic style is preferred.

Graphic adaptations such as trees in the background would be of interest.
Should not have
• Colour scheme should not be gray scale.

The banners should NOT be too busy.

Scripture verses (written out) are not necessary.

```html
<!DOCTYPE html>
<html lang="en">
<head>
<meta charset="utf-8">
<title>Meadowfield Baptist Church – Auditorium Banners</title>
<link rel="stylesheet" href="https://fonts.googleapis.com/css2?family=Montserrat:wght@700;800&display=swap">
<style>
  :root {
    --stage: #262626;
    --ink-shadow: #4a4e50;
    --mark-blue: #78bdca;
    --white: #ffffff;

    --truth-main: #7bbcc8;
    --truth-deep: #0b788c;
    --love-main: #1fa98f;
    --love-deep: #0d5b38;
    --mission-main: #e67c3e;
    --mission-deep: #d8523a;
  }
  * { margin: 0; padding: 0; box-sizing: border-box; }
  html, body {
    width: 1200px; height: 909px; overflow: hidden;
    background: var(--stage);
  }
  .banner-set {
    position: relative; width: 1200px; height: 909px;
  }
  .banner {
    position: absolute; top: 45px; width: 322px; height: 805px;
    overflow: hidden;
    box-shadow: 0 6px 18px rgba(0,0,0,.55);
  }
  .banner--truth   { left: 47px;  background: linear-gradient(180deg, var(--truth-main) 0%, var(--truth-main) 62%, var(--truth-deep) 100%); }
  .banner--love    { left: 440px; background: linear-gradient(180deg, var(--love-main) 0%, var(--love-main) 62%, var(--love-deep) 100%); }
  .banner--mission { left: 832px; background: linear-gradient(180deg, var(--mission-main) 0%, var(--mission-main) 62%, var(--mission-deep) 100%); }

  .banner__waves { position: absolute; left: 0; top: 0; width: 322px; height: 420px; }

  .church-name {
    position: absolute; left: 0; top: 150px; width: 322px;
    display: flex; flex-direction: column; align-items: center; gap: 10px;
    font-family: "Montserrat", sans-serif; font-weight: 700;
    color: var(--mark-blue); text-align: center;
    font-size: 17px; line-height: 1.2; letter-spacing: .04em;
  }
  .church-name__dot {
    width: 54px; height: 54px; border-radius: 50%;
    border: 4px solid var(--mark-blue);
  }

  .banner__word {
    position: absolute; left: 0; top: 456px; width: 322px;
    text-align: center;
    font-family: "Montserrat", sans-serif; font-weight: 800;
    font-size: 52px; line-height: 1; letter-spacing: .01em;
    color: var(--white);
    text-shadow: 2px 2px 0 var(--ink-shadow), 3px 3px 0 var(--ink-shadow), 4px 4px 0 var(--ink-shadow), 6px 6px 4px rgba(0,0,0,.2);
  }

  .banner__forest {
    position: absolute; left: 4px; bottom: 0; width: 314px; height: 275px;
    background: linear-gradient(180deg, rgba(255,255,255,0) 0%, rgba(255,255,255,.55) 40%, rgba(255,255,255,.8) 100%);
    clip-path: polygon(0 100%, 2% 45%, 17% 35%, 30% 55%, 42% 35%, 66% 0, 74% 40%, 88% 55%, 100% 60%, 100% 100%);
  }
</style>
</head>
<body>
<main class="banner-set">

  <section class="banner banner--truth">
    <svg class="banner__waves" viewBox="0 0 322 420" aria-hidden="true">
      <defs>
        <radialGradient id="glow-truth" cx="50%" cy="50%" r="70%">
          <stop offset="45%" stop-color="#ffffff"/>
          <stop offset="100%" stop-color="#a7d3de"/>
        </radialGradient>
      </defs>
      <path d="M0 330 Q40 318 80 326 T160 330 T240 328 T322 320 L322 395 Q290 410 240 402 T160 404 T80 402 T0 392 Z" fill="#c2e1e6"/>
      <path d="M0 50 Q40 62 80 56 T160 56 T240 56 T322 48 L322 355 Q290 370 240 363 T160 365 T80 363 T0 352 Z" fill="url(#glow-truth)"/>
    </svg>
    <div class="church-name"><span class="church-name__dot"></span><span>Meadowfield<br>Baptist Church</span></div>
    <h2 class="banner__word">TRUTH</h2>
    <div class="banner__forest" role="img" aria-label="White silhouette of evergreen pine trees"></div>
  </section>

  <section class="banner banner--love">
    <svg class="banner__waves" viewBox="0 0 322 420" aria-hidden="true">
      <defs>
        <radialGradient id="glow-love" cx="50%" cy="50%" r="70%">
          <stop offset="40%" stop-color="#ffffff"/>
          <stop offset="100%" stop-color="#7cc5ab"/>
        </radialGradient>
      </defs>
      <path d="M0 330 Q40 318 80 326 T160 330 T240 328 T322 320 L322 395 Q290 410 240 402 T160 404 T80 402 T0 392 Z" fill="#b9d8cf"/>
      <path d="M0 50 Q40 62 80 56 T160 56 T240 56 T322 48 L322 355 Q290 370 240 363 T160 365 T80 363 T0 352 Z" fill="url(#glow-love)"/>
    </svg>
    <div class="church-name"><span class="church-name__dot"></span><span>Meadowfield<br>Baptist Church</span></div>
    <h2 class="banner__word">LOVE</h2>
    <div class="banner__forest" role="img" aria-label="White silhouette of evergreen pine trees"></div>
  </section>

  <section class="banner banner--mission">
    <svg class="banner__waves" viewBox="0 0 322 420" aria-hidden="true">
      <defs>
        <radialGradient id="glow-mission" cx="50%" cy="50%" r="70%">
          <stop offset="40%" stop-color="#ffffff"/>
          <stop offset="100%" stop-color="#eea16b"/>
        </radialGradient>
      </defs>
      <path d="M0 330 Q40 318 80 326 T160 330 T240 328 T322 320 L322 395 Q290 410 240 402 T160 404 T80 402 T0 392 Z" fill="#e8b89b"/>
      <path d="M0 50 Q40 62 80 56 T160 56 T240 56 T322 48 L322 355 Q290 370 240 363 T160 365 T80 363 T0 352 Z" fill="url(#glow-mission)"/>
    </svg>
    <div class="church-name"><span class="church-name__dot"></span><span>Meadowfield<br>Baptist Church</span></div>
    <h2 class="banner__word">MISSION</h2>
    <div class="banner__forest" role="img" aria-label="White silhouette of evergreen pine trees"></div>
  </section>

</main>
</body>
</html>
```